Skiing Company Needs A5 28page Skiing Catalogue

ABOUT THE BUSINESS/COMPANY:
- We are a guided skiing company called "Silver Lantern Journeys" and "Kestrel Ridge Alpine Society".

ABOUT THE CATALOGUE:

- We need an A5 28 page catalogue. ALL THE FILES (like photos and logos) are in the zip folders.

- You can look at the 000 KRS Catalog Word Document. Instructions on what text and photos to use are labeled there per Page.

Target Market(s)

Advanced/ Expert Skiers and Snowboarders that are thinking of joining a tour

Industry/Entity Type

Travel Agent

Font styles to use
Serif

Colors
ffffff
ec1f27
0455a3

Requirements
Must have
• NEED a 3mm bleed
• This is included on the 000 KRS Catalog word document
Nice to have
• Our main color is dark blue (just like our logo). Some red is ok but the main focus should be the dark blue.
Should not have
• Words/ Letters in the color red

```html
<!DOCTYPE html>
<html lang="en">
<head>
<meta charset="utf-8">
<title>Silver Lantern Journeys — 2017-2018 Product Catalog Cover Spread</title>
<link rel="stylesheet" href="https://fonts.googleapis.com/css2?family=Montserrat:wght@300;400;700&display=swap">
<style>
  :root {
    --brand-blue: #0455a3;
    --cover-blue: #0753a6;
    --band-dark: #2b2a2a;
    --paper: #ffffff;
    --stage: #eceae6;
  }
  html, body {
    margin: 0;
    padding: 0;
    width: 1200px;
    height: 1200px;
    overflow: hidden;
    background: var(--stage);
  }
  .spread {
    position: absolute;
    left: 40px;
    top: 204px;
    width: 1120px;
    height: 792px;
    box-shadow: 0 6px 18px rgba(0,0,0,0.18);
  }
  .spread svg {
    display: block;
    width: 100%;
    height: 100%;
  }
  .cover-year {
    font-family: "Montserrat", sans-serif;
    font-weight: 700;
    fill: var(--brand-blue);
  }
  .cover-title {
    font-family: "Montserrat", sans-serif;
    font-weight: 400;
    fill: var(--brand-blue);
    letter-spacing: 1px;
  }
  .brand-name {
    font-family: "Montserrat", sans-serif;
    font-weight: 700;
    fill: var(--brand-blue);
  }
</style>
</head>
<body>
  <div class="spread">
    <svg viewBox="0 0 1250 884" xmlns="http://www.w3.org/2000/svg">
      <defs>
        <linearGradient id="skier-photo-tone" x1="0" y1="0" x2="1" y2="0.4">
          <stop offset="0" stop-color="#ffffff"/>
          <stop offset="0.35" stop-color="#e6e6e6"/>
          <stop offset="0.62" stop-color="#3a3a3a"/>
          <stop offset="1" stop-color="#050505"/>
        </linearGradient>
        <linearGradient id="mountain-photo-tone" x1="0" y1="0" x2="0.7" y2="1">
          <stop offset="0" stop-color="#dfe6ee"/>
          <stop offset="0.4" stop-color="#f4f6f9"/>
          <stop offset="0.75" stop-color="#d3dce7"/>
          <stop offset="1" stop-color="#b9c6d6"/>
        </linearGradient>
        <linearGradient id="spine-fade" x1="0" y1="0" x2="1" y2="0">
          <stop offset="0" stop-color="#dedede"/>
          <stop offset="0.18" stop-color="#ffffff"/>
        </linearGradient>
      </defs>

      <g class="back-cover">
        <rect class="back-cover__blue" x="0" y="0" width="625" height="884" fill="var(--cover-blue)"/>
        <polygon class="back-cover__photo" role="img"
                 aria-label="Black and white photo of a skier carving through deep powder, backlit spray"
                 points="0,296 625,559 625,884 0,884" fill="url(#skier-photo-tone)"/>
      </g>

      <g class="front-cover">
        <rect class="front-cover__paper" x="625" y="0" width="625" height="884" fill="url(#spine-fade)"/>
        <polygon class="front-cover__photo" role="img"
                 aria-label="Photo of a snowy volcano with a lone skier descending a powder slope among frosted trees"
                 points="625,0 1250,0 1250,705 995,600 995,715 625,559" fill="url(#mountain-photo-tone)"/>

        <g class="front-cover__brands">
          <circle cx="974" cy="95" r="7" fill="var(--brand-blue)"/>
          <text class="brand-name" x="988" y="100" font-size="13">Kestrel Ridge Alpine Society</text>
          <text class="brand-name" x="988" y="124" font-size="13">Silver Lantern Journeys</text>
        </g>

        <text class="cover-year" x="673" y="770" font-size="44">2017-2018</text>
        <text class="cover-title" x="673" y="808" font-size="30">PRODUCT CATALOG</text>
      </g>

      <polyline class="ridge-band" points="-10,292 995,715 995,600 1262,710"
                fill="none" stroke="var(--band-dark)" stroke-width="28" stroke-linejoin="miter" stroke-miterlimit="10"/>
    </svg>
  </div>
</body>
</html>
```